Larkspur Talent IT Recruiting firm needs a business card design for Recruiters, Sourcers, and Account

We need business cards that allow us to change all contact info, names, titles (Recruiter, Sourcer, Account Manager, Director, CEO, etc) per person since we have three offices, in three cities, Phoenix, Austin, and Las Vegas. We do recruiting and contractors for IT positions (Developers, Architects, Software Engineers, Security Engineers, Help Desk, DBAs, PMs, Scrum Masters, etc.) Our client companies are very diverse from Meridian 100 to silicone Valley type start-ups.

So, while we what hip, techie, and quirky, it still needs to be professional. Primary color we use is blue, with silver as a secondary color.

Target Market(s)

IT, Technology

Industry/Entity Type

Business

Contact Information for Business Card

Company name: Larkspur Talent, Inc.
Website: www.larkspurtalent.example
Logos for Careerloop, Blipster, and Myriada

Name, Title, Office Number, Cell Number, email

Font styles to use
Serif
Sans Serif

Colors
0455a3
d5d5d5

Requirements
Nice to have
• The grey I selected below is not necessary - but, would like silver included. I included a card design (File 3: LTI early trial example.jpg) that I had started on. It's very rough, and not quite what we're looking for, but what we did like is the logo, big, maybe a bit faded, off center, goes out of frame, etc. Still looking for other ideas - you are the pros! But, just an idea of a design element we liked.

```html
<!DOCTYPE html>
<html lang="en">
<head>
<meta charset="utf-8">
<title>Larkspur Talent – Business Card</title>
<link rel="stylesheet" href="https://fonts.googleapis.com/css2?family=Cinzel:wght@400;600&family=Open+Sans:wght@400;700&display=swap">
<style>
  :root {
    --backdrop: #4a4a4c;
    --card-dark: #0b0c0e;
    --card-mid: #1a1b1e;
    --faint-mark: rgba(255,255,255,0.045);
    --blue: #0a8fde;
    --blue-deep: #0455a3;
    --white: #ffffff;
    --silver: #d5d5d5;
  }
  * { box-sizing: border-box; margin: 0; padding: 0; }
  html, body { width: 1200px; height: 852px; overflow: hidden; }
  body {
    background: var(--backdrop);
    font-family: "Open Sans", Arial, sans-serif;
    position: relative;
  }
  .card {
    position: absolute;
    width: 540px;
    height: 309px;
    border-radius: 14px;
    overflow: hidden;
    background: linear-gradient(160deg, var(--card-mid) 0%, var(--card-dark) 70%);
    box-shadow: 0 10px 30px rgba(0,0,0,0.45);
  }
  .card--front { left: 40px; top: 272px; }
  .card--back  { left: 620px; top: 272px; }

  .faint-mark {
    position: absolute;
    border-radius: 50%;
    border: 46px solid var(--faint-mark);
  }
  .card--front .faint-mark { width: 420px; height: 420px; left: -90px; top: -60px; }
  .card--back .faint-mark  { width: 380px; height: 380px; left: 170px; top: -40px; }

  .wordmark { position: absolute; }
  .wordmark__name {
    display: flex; align-items: center; gap: 10px;
    font-family: "Cinzel", "Times New Roman", serif;
    color: var(--white); font-weight: 600; letter-spacing: 0.03em; line-height: 1;
    white-space: nowrap;
  }
  .wordmark__dot { border-radius: 50%; background: var(--blue); flex: none; }
  .wordmark__rule { height: 2px; background: var(--blue); }
  .wordmark__tagline {
    font-family: "Open Sans", Arial, sans-serif;
    color: var(--silver); letter-spacing: 0.18em; text-transform: uppercase;
    white-space: nowrap;
  }

  .card--front .wordmark { left: 60px; top: 112px; width: 420px; }
  .card--front .wordmark__name { font-size: 36px; }
  .card--front .wordmark__dot { width: 26px; height: 26px; }
  .card--front .wordmark__rule { width: 120px; margin: 18px 0 0 36px; }
  .card--front .wordmark__tagline { font-size: 12px; margin: 14px 0 0 36px; }

  .card--back .wordmark { right: 26px; top: 30px; text-align: right; }
  .card--back .wordmark__name { font-size: 21px; justify-content: flex-end; gap: 7px; }
  .card--back .wordmark__dot { width: 15px; height: 15px; }
  .card--back .wordmark__rule { width: 70px; margin: 10px 0 0 auto; }
  .card--back .wordmark__tagline { font-size: 8px; margin-top: 8px; }

  .side-band { position: absolute; left: 0; top: 0; bottom: 0; width: 44px; background: var(--blue); }

  .person { position: absolute; left: 68px; top: 108px; }
  .person__name { color: var(--blue); font-weight: 700; font-size: 14px; letter-spacing: 0.02em; }
  .person__title { color: var(--white); font-size: 10px; margin-top: 3px; }

  .social { position: absolute; right: 24px; top: 120px; display: flex; gap: 10px; }
  .social__item { display: flex; align-items: center; gap: 4px; color: var(--blue); font-size: 9px; font-weight: 700; }
  .social__item::before { content: ""; width: 9px; height: 9px; border-radius: 2px; background: var(--blue); }

  .address { position: absolute; left: 68px; top: 178px; color: var(--white); font-size: 12px; line-height: 1.45; }

  .contact { position: absolute; left: 68px; top: 222px; list-style: none; }
  .contact li { display: flex; align-items: center; gap: 10px; color: var(--white); font-size: 12px; line-height: 18px; }
  .contact svg { width: 12px; height: 12px; flex: none; fill: var(--silver); }
</style>
</head>
<body>

<section class="card card--front" aria-label="Card front">
  <div class="faint-mark"></div>
  <div class="wordmark">
    <div class="wordmark__name"><span class="wordmark__dot"></span>Larkspur Talent</div>
    <div class="wordmark__rule"></div>
    <div class="wordmark__tagline">Talent That Moves Tech Forward</div>
  </div>
</section>

<section class="card card--back" aria-label="Card back">
  <div class="faint-mark"></div>
  <div class="side-band"></div>

  <div class="wordmark">
    <div class="wordmark__name"><span class="wordmark__dot"></span>Larkspur Talent</div>
    <div class="wordmark__rule"></div>
    <div class="wordmark__tagline">Talent That Moves Tech Forward</div>
  </div>

  <div class="person">
    <div class="person__name">DANA WHITFORD</div>
    <div class="person__title">CEO</div>
  </div>

  <div class="social">
    <span class="social__item">Blipster</span>
    <span class="social__item">Careerloop</span>
    <span class="social__item">Myriada</span>
  </div>

  <div class="address">
    4820 Harlow Ave, Suite 210<br>
    Mesa Ridge, AZ 85000, USA
  </div>

  <ul class="contact">
    <li>
      <svg viewBox="0 0 24 24" aria-hidden="true"><path d="M6.6 10.8a15.1 15.1 0 0 0 6.6 6.6l2.2-2.2c.3-.3.7-.4 1-.2 1.1.4 2.3.6 3.6.6.6 0 1 .4 1 1V20c0 .6-.4 1-1 1A17 17 0 0 1 3 4c0-.6.4-1 1-1h3.5c.6 0 1 .4 1 1 0 1.3.2 2.5.6 3.6.1.3 0 .7-.2 1z"/></svg>
      555| 010-4821
    </li>
    <li>
      <svg viewBox="0 0 24 24" aria-hidden="true"><path d="M7 1h10a2 2 0 0 1 2 2v18a2 2 0 0 1-2 2H7a2 2 0 0 1-2-2V3a2 2 0 0 1 2-2zm0 3v14h10V4zm5 15.5a1.2 1.2 0 1 0 0 2.4 1.2 1.2 0 0 0 0-2.4z"/></svg>
      555| 014-7730
    </li>
    <li>
      <svg viewBox="0 0 24 24" aria-hidden="true"><path d="M2 5h20v14H2zm2 2v.5l8 5 8-5V7zm0 2.9V17h16V9.9l-8 5z"/></svg>
      dana@larkspurtalent.example
    </li>
    <li>
      <svg viewBox="0 0 24 24" aria-hidden="true"><path d="M12 2a10 10 0 1 0 0 20 10 10 0 0 0 0-20zm6.9 6h-3a15 15 0 0 0-1.3-3.9A8 8 0 0 1 18.9 8zM12 4c.8 1.2 1.5 2.5 1.9 4h-3.8c.4-1.5 1.1-2.8 1.9-4zM4.3 14a8 8 0 0 1 0-4h3.4a16 16 0 0 0 0 4zm.8 2h3a15 15 0 0 0 1.3 3.9A8 8 0 0 1 5.1 16zm3-8h-3a8 8 0 0 1 4.3-3.9A15 15 0 0 0 8.1 8zM12 20c-.8-1.2-1.5-2.5-1.9-4h3.8c-.4 1.5-1.1 2.8-1.9 4zm2.3-6H9.7a14 14 0 0 1 0-4h4.6a14 14 0 0 1 0 4zm.3 5.9a15 15 0 0 0 1.3-3.9h3a8 8 0 0 1-4.3 3.9zM16.3 14a16 16 0 0 0 0-4h3.4a8 8 0 0 1 0 4z"/></svg>
      www.larkspurtalent.example
    </li>
  </ul>
</section>

</body>
</html>
```